Super elegant, crisp & clean Business card design required

We recently upgraded our branding - which is on our website - talvendoraphoto.com

I would like a simple, yet elegant, clean business card design please.

The font of my logo is Cinzel - and because of the natural colour - it's best to have this on a black background.

I would like to have the back of the business card - with simply my logo.

PLEASE DO NOT SUBMIT A COMPLICATED / UNCLEAN DESIGN

Industry/Entity Type

Business

Contact Information for Business Card

Talven Doroshko Photography

Font styles to use
Other font styles liked:
• Cinzel

Requirements
Must have
• A backpage with nothing but my logo
• Simple design - stands out
Should not have
• Colour that dont align with my logo
• Over complicated '/ non symmetrical design

```html
<!DOCTYPE html>
<html lang="en">
<head>
<meta charset="utf-8">
<title>Talven Doroshko Photography – Business Card</title>
<link rel="stylesheet" href="https://fonts.googleapis.com/css2?family=Cinzel:wght@400&family=Libre+Baskerville:wght@700&display=swap">
<style>
  :root {
    --backdrop: #dcdcdc;
    --card-black: #0d0d0d;
    --card-white: #ffffff;
    --gold: #7d6c55;
    --gold-deep: #6b5c49;
    --card-edge: #7a6a56;
  }
  * { margin: 0; padding: 0; box-sizing: border-box; }
  html, body {
    width: 1200px;
    height: 900px;
    overflow: hidden;
    background: var(--backdrop);
  }
  .canvas {
    position: relative;
    width: 1200px;
    height: 900px;
  }
  .card {
    position: absolute;
    left: 303px;
    width: 637px;
    height: 367px;
    border: 1px solid var(--card-edge);
  }
  .card--front {
    top: 38px;
    background: var(--card-black);
  }
  .card--back {
    top: 478px;
    background: var(--card-white);
  }
  .brand-name,
  .brand-tagline {
    font-family: "Cinzel", serif;
    font-weight: 400;
    color: var(--gold);
    white-space: nowrap;
  }
  .brand-name { font-size: 29px; letter-spacing: 0.5px; }
  .brand-tagline { font-size: 13px; letter-spacing: 6.5px; }

  /* Front */
  .front-mark {
    position: absolute;
    left: 50%;
    top: 80px;
    width: 80px;
    height: 80px;
    margin-left: -40px;
    border: 1.5px solid var(--gold);
    border-radius: 50%;
  }
  .front-lockup {
    position: absolute;
    left: 0;
    right: 0;
    top: 238px;
    text-align: center;
  }
  .front-lockup .brand-tagline { margin-top: 2px; }

  /* Back */
  .back-mark {
    position: absolute;
    left: 28px;
    top: 42px;
    width: 66px;
    height: 66px;
    border: 1.5px solid var(--gold);
    border-radius: 50%;
  }
  .back-lockup {
    position: absolute;
    left: 103px;
    top: 52px;
  }
  .back-lockup .brand-tagline { margin-left: 36px; margin-top: 2px; }

  .contact-list {
    position: absolute;
    left: 362px;
    top: 236px;
    list-style: none;
  }
  .contact-item {
    display: flex;
    align-items: center;
    height: 35px;
    font-family: "Libre Baskerville", serif;
    font-weight: 700;
    font-size: 15.5px;
    color: var(--gold-deep);
  }
  .contact-icon {
    width: 24px;
    height: 24px;
    margin-right: 14px;
    flex: none;
  }
</style>
</head>
<body>
<main class="canvas">

  <section class="card card--front" aria-label="Card front">
    <div class="front-mark" aria-hidden="true"></div>
    <div class="front-lockup">
      <div class="brand-name">Talven Doroshko</div>
      <div class="brand-tagline">PHOTOGRAPHY</div>
    </div>
  </section>

  <section class="card card--back" aria-label="Card back">
    <div class="back-mark" aria-hidden="true"></div>
    <div class="back-lockup">
      <div class="brand-name">Talven Doroshko</div>
      <div class="brand-tagline">PHOTOGRAPHY</div>
    </div>

    <ul class="contact-list">
      <li class="contact-item">
        <svg class="contact-icon" viewBox="0 0 24 24" aria-hidden="true">
          <path fill="#6b5c49" d="M6.6 3.2c.6-.4 1.4-.3 1.8.3l2 3c.4.6.3 1.3-.2 1.7l-1.3 1.1c.9 2 2.5 3.6 4.5 4.6l1.1-1.3c.4-.5 1.2-.6 1.7-.2l3 2c.6.4.7 1.2.3 1.8l-1.1 1.6c-.6.9-1.7 1.3-2.8 1-5.3-1.5-9.5-5.7-11-11-.3-1.1.1-2.2 1-2.8z"/>
        </svg>
        <span>123 456 789</span>
      </li>
      <li class="contact-item">
        <svg class="contact-icon" viewBox="0 0 24 24" aria-hidden="true" fill="none" stroke="#6b5c49" stroke-width="1.6">
          <circle cx="12" cy="12" r="9.5"/>
          <ellipse cx="12" cy="12" rx="4.2" ry="9.5"/>
          <line x1="12" y1="2.5" x2="12" y2="21.5"/>
          <line x1="2.5" y1="12" x2="21.5" y2="12"/>
          <path d="M4.3 7h15.4M4.3 17h15.4"/>
        </svg>
        <span>talvendoraphoto.com</span>
      </li>
      <li class="contact-item">
        <svg class="contact-icon" viewBox="0 0 24 24" aria-hidden="true">
          <rect x="1.5" y="5" width="21" height="14" fill="#6b5c49"/>
          <path d="M1.5 5.5 12 13.5 22.5 5.5" fill="none" stroke="#ffffff" stroke-width="1.4"/>
        </svg>
        <span>lorem@ipsum.com</span>
      </li>
    </ul>
  </section>

</main>
</body>
</html>
```